Lawn sign for construction company

Would like this to be a very clean and high end design for luxury homes. We need a yard sign designed that includes the company logo, website, phone number and major service offerings (residential and commercial renovations and maintenance)
The company website is brackwellbuilders.com all other contact info is in the attachments
Target Market(s)
Luxury home owners and business owners
Industry/Entity Type
Construction/Home Improvement
Font styles to use
Other font styles liked:
- See company logo and other graphics included for title text fonts. All other fonts can be standard sans serif.
Colors
0054AA
0677BA
7BADD7
CADEEF
E8F1F8
Requirements
Must have
- Clean, easy to read design, would like 2 sided sign. A main sign side and back side which states “free estimates, and includes the website and phone number. Must also match the color scheme of the provided logo and other company images. Dark Navy blue primary color, gray secondary color, and orange as an accent color.
Nice to have
- 2nd sign side very simple design
Should not have
- Too many graphics limit to 1-3 colors

```html
<!DOCTYPE html>
<html lang="en">
<head>
<meta charset="utf-8">
<title>Brackwell Builders Yard Sign</title>
<link href="https://fonts.googleapis.com/css2?family=Oswald:wght@500;600&family=Montserrat:wght@700;800;900&display=swap" rel="stylesheet">
<style>
  :root {
    --navy: #0d2449;
    --orange: #f07f0a;
    --gray: #6b6b6b;
    --white: #ffffff;
    --backdrop: #5b5b5b;
  }
  html, body {
    margin: 0;
    padding: 0;
    width: 1200px;
    height: 2644px;
    overflow: hidden;
    background: var(--backdrop);
  }
  .sign {
    position: absolute;
    left: 80px;
    width: 1040px;
    height: 790px;
    background: var(--white);
    overflow: hidden;
  }
  .sign--front { top: 300px; }
  .sign--back { top: 1290px; }
  .sign-band {
    position: absolute;
    left: 0;
    top: 0;
    width: 1040px;
    height: 790px;
  }
  .sign-text {
    position: absolute;
    left: 0;
    width: 100%;
    text-align: center;
    white-space: nowrap;
    line-height: 1;
    margin: 0;
  }
  .brand-name {
    top: 215px;
    display: flex;
    justify-content: center;
    align-items: center;
    gap: 26px;
    font-family: "Oswald", sans-serif;
    font-weight: 600;
    font-size: 86px;
    color: var(--orange);
    letter-spacing: 1px;
  }
  .brand-dot {
    width: 64px;
    height: 64px;
    border-radius: 50%;
    background: var(--gray);
  }
  .service-lead {
    top: 530px;
    font-family: "Oswald", sans-serif;
    font-weight: 600;
    font-size: 58px;
    color: var(--orange);
  }
  .service-main {
    top: 588px;
    font-family: "Oswald", sans-serif;
    font-weight: 600;
    font-size: 118px;
    color: var(--orange);
    letter-spacing: 1px;
  }
  .service-detail {
    top: 712px;
    font-family: "Oswald", sans-serif;
    font-weight: 500;
    font-size: 56px;
    color: var(--white);
  }
  .offer-headline {
    top: 90px;
    font-family: "Montserrat", sans-serif;
    font-weight: 900;
    font-size: 262px;
    color: var(--orange);
    letter-spacing: -4px;
  }
  .offer-sub {
    top: 340px;
    font-family: "Montserrat", sans-serif;
    font-weight: 900;
    font-size: 112px;
    color: var(--navy);
    letter-spacing: -2px;
  }
  .contact-row {
    display: flex;
    justify-content: center;
    align-items: center;
    gap: 34px;
    font-family: "Montserrat", sans-serif;
    color: var(--white);
  }
  .contact-web {
    top: 575px;
    font-weight: 700;
    font-size: 50px;
  }
  .contact-phone {
    top: 652px;
    font-weight: 800;
    font-size: 92px;
    letter-spacing: -1px;
  }
  .contact-icon { flex: none; }
  .contact-web .contact-icon { width: 44px; height: 44px; }
  .contact-phone .contact-icon { width: 56px; height: 56px; }
</style>
</head>
<body>

<section class="sign sign--front">
  <svg class="sign-band" viewBox="0 0 1040 790" aria-hidden="true">
    <path d="M0 592 Q520 388 1040 592 L1040 790 L0 790 Z" fill="var(--orange)"/>
    <path d="M0 632 Q520 410 1040 632 L1040 790 L0 790 Z" fill="var(--navy)"/>
  </svg>
  <div class="sign-text brand-name"><span class="brand-dot"></span>BRACKWELL BUILDERS</div>
  <p class="sign-text service-lead">RESIDENTIAL &amp;</p>
  <p class="sign-text service-main">COMMERCIAL</p>
  <p class="sign-text service-detail">RENOVATIONS AND MAINTENANCE</p>
</section>

<section class="sign sign--back">
  <svg class="sign-band" viewBox="0 0 1040 790" aria-hidden="true">
    <path d="M0 592 Q520 388 1040 592 L1040 790 L0 790 Z" fill="var(--orange)"/>
    <path d="M0 632 Q520 410 1040 632 L1040 790 L0 790 Z" fill="var(--navy)"/>
  </svg>
  <p class="sign-text offer-headline">FREE</p>
  <p class="sign-text offer-sub">ESTIMATES</p>
  <div class="sign-text contact-row contact-web">
    <svg class="contact-icon" viewBox="0 0 24 24" aria-hidden="true" fill="none" stroke="var(--orange)" stroke-width="2">
      <circle cx="12" cy="12" r="10"/>
      <ellipse cx="12" cy="12" rx="4.5" ry="10"/>
      <line x1="2" y1="12" x2="22" y2="12"/>
      <line x1="4" y1="7" x2="20" y2="7"/>
      <line x1="4" y1="17" x2="20" y2="17"/>
    </svg>
    <span>brackwellbuilders.com</span>
  </div>
  <div class="sign-text contact-row contact-phone">
    <svg class="contact-icon" viewBox="0 0 24 24" aria-hidden="true">
      <path fill="var(--orange)" d="M6.6 10.8c1.4 2.8 3.8 5.1 6.6 6.6l2.2-2.2c.3-.3.7-.4 1-.2 1.1.4 2.3.6 3.6.6.6 0 1 .4 1 1V20c0 .6-.4 1-1 1C10.6 21 3 13.4 3 4c0-.6.4-1 1-1h3.5c.6 0 1 .4 1 1 0 1.3.2 2.5.6 3.6.1.3 0 .7-.2 1z"/>
      <path fill="none" stroke="var(--orange)" stroke-width="1.8" stroke-linecap="round" d="M14 3.5a6.5 6.5 0 0 1 6.5 6.5M14 7a3 3 0 0 1 3 3"/>
    </svg>
    <span>810-555-0173</span>
  </div>
</section>

</body>
</html>
```